American cannabis tech company business card design

Pavrel.com is seeking a modern, professional, and brand-aligned business card that represents our company and its core values: Mission, Story, Values, and Impact. As an innovative cannabis company, we want a business card that is not only visually appealing but also serves as a representation of who we are and what we stand for.

Project Scope: Design a double-sided business card that integrates our brand identity and core values. Incorporate our key brand elements, ensuring a sleek and contemporary aesthetic. Visually reflect our core values (Mission, Story, Values, Impact) in a way that is engaging yet professional.

Target Market(s)

Vendors, third parties,

Contact Information for Business Card

Contact details (name, title, email, phone, website, etc.)

Font styles to use
Other font styles liked:
• Caslon, Centra

Colors

Designer to choose colors to be used in the design.

Requirements
Must have
• Pavrel.com logo and branding A creative yet clean way to integrate our core values (Mission, Story, Values, Impact) Modern typography and a well-structured layout
Nice to have
• forest green, grey, white, black
Should not have
• references to marijuana, leafs, plants, or related product

```html
<!DOCTYPE html>
<html lang="en">
<head>
<meta charset="utf-8">
<title>Pavrel.com Business Card</title>
<link href="https://fonts.googleapis.com/css2?family=Libre+Caslon+Text:wght@700&family=Montserrat:wght@400&display=swap" rel="stylesheet">
<style>
  :root {
    --forest: #1b3220;
    --paper: #ffffff;
    --cream: #fbf8f0;
    --ink: #1d1d1d;
    --backdrop: #2a2a2a;
    --backdrop-edge: #0c0c0c;
  }
  * { box-sizing: border-box; margin: 0; padding: 0; }
  html, body { width: 1200px; height: 1015px; overflow: hidden; }
  body {
    background: radial-gradient(ellipse at center, var(--backdrop) 0%, var(--backdrop-edge) 100%);
    display: flex;
    flex-direction: column;
    align-items: center;
    justify-content: center;
    gap: 60px;
  }
  .card {
    width: 680px;
    height: 388px;
    position: relative;
    box-shadow: 0 12px 30px rgba(0,0,0,0.55);
  }
  .card--front {
    background: var(--forest);
    display: flex;
    align-items: center;
    justify-content: center;
  }
  .brand {
    display: flex;
    align-items: center;
    gap: 14px;
    font-family: "Montserrat", Arial, sans-serif;
    font-weight: 400;
    line-height: 1;
  }
  .brand__dot { border-radius: 50%; flex: none; }
  .card--front .brand { color: var(--cream); font-size: 48px; }
  .card--front .brand__dot { width: 22px; height: 22px; background: var(--cream); }
  .card--back { background: var(--paper); color: var(--ink); }
  .card--back .brand {
    position: absolute;
    right: 56px;
    top: 104px;
    color: var(--forest);
    font-size: 36px;
  }
  .card--back .brand__dot { width: 16px; height: 16px; background: var(--forest); }
  .holder {
    position: absolute;
    left: 48px;
    top: 96px;
    font-family: "Libre Caslon Text", Georgia, serif;
    font-weight: 700;
    color: var(--forest);
  }
  .holder__name { font-size: 20px; }
  .holder__title { font-size: 11px; color: var(--ink); margin-top: 2px; }
  .address {
    position: absolute;
    left: 160px;
    top: 214px;
    font-family: "Montserrat", Arial, sans-serif;
    font-style: normal;
    font-size: 14px;
    line-height: 1.25;
  }
  .contacts {
    position: absolute;
    left: 160px;
    top: 266px;
    list-style: none;
    font-family: "Montserrat", Arial, sans-serif;
    font-size: 14px;
    line-height: 1.6;
  }
  .contacts li { display: flex; align-items: center; gap: 8px; }
  .contacts svg { width: 11px; height: 11px; fill: var(--forest); flex: none; }
</style>
</head>
<body>
  <section class="card card--front">
    <span class="brand"><span class="brand__dot"></span>Pavrel</span>
  </section>

  <section class="card card--back">
    <div class="holder">
      <p class="holder__name">Dana Whitfield</p>
      <p class="holder__title">Owner</p>
    </div>
    <span class="brand"><span class="brand__dot"></span>Pavrel</span>
    <address class="address">
      415 Harlow Ave, Suite 12<br>
      Brookfield, OH 43100
    </address>
    <ul class="contacts">
      <li>
        <svg viewBox="0 0 24 24" aria-hidden="true"><path d="M6.6 10.8a15.1 15.1 0 0 0 6.6 6.6l2.2-2.2a1 1 0 0 1 1-.25 11.4 11.4 0 0 0 3.6.57 1 1 0 0 1 1 1V20a1 1 0 0 1-1 1A17 17 0 0 1 3 4a1 1 0 0 1 1-1h3.5a1 1 0 0 1 1 1c0 1.25.2 2.45.57 3.6a1 1 0 0 1-.25 1z"/></svg>
        555-318-0427
      </li>
      <li>
        <svg viewBox="0 0 24 24" aria-hidden="true"><rect x="2" y="5" width="20" height="14" rx="1"/></svg>
        info@pavrel.com
      </li>
      <li>
        <svg viewBox="0 0 24 24" aria-hidden="true"><circle cx="12" cy="12" r="10"/></svg>
        www.pavrel.com
      </li>
    </ul>
  </section>
</body>
</html>
```